New Business Card Design Project

We require a business card design for Vexalund, a newly established Indian company.
Our focus is on the development, manufacturing, and export of a diverse array of pharmaceutical products on a global scale. The card should convey a professional appearance, as our primary markets are in Africa, China, and Southeast Asian nations.
We envision a two-sided business card, with the reverse side dedicated to a logo set against a solid color or an elegantly designed pattern. The corners should be rounded. We would appreciate seeing both horizontal and vertical design options. We trust the designer to utilize their expertise in creating this design.

The content for the business card is included in the attached Word file.

Target Market(s)

Our primary markets are in Africa, China, and Southeast Asian, Latin America, Maldives, Sri Lanka

Industry/Entity Type

Pharmaceutical Manufacturing and Export

Contact Information for Business Card

Colors

Designer to choose colors to be used in the design.

Requirements
Must have
• The reverse side of the business card features solely the logo along with the tagline, "Remedies of Life."
Should not have
• The logo should not exceed two instances, encompassing both the front and back sides of the card.

```html
<!DOCTYPE html>
<html lang="en">
<head>
<meta charset="utf-8">
<title>Vexalund Business Card</title>
<link rel="stylesheet" href="https://fonts.googleapis.com/css2?family=Montserrat:wght@500;700;800&family=Open+Sans:wght@400;600;700&display=swap">
<style>
  :root {
    --stage: #232323;
    --card: #ffffff;
    --blue: #29a6e0;
    --coral: #f0634d;
    --ink: #1d1d1d;
  }
  * { box-sizing: border-box; margin: 0; padding: 0; }
  html, body { width: 1200px; height: 711px; overflow: hidden; }
  body {
    background: var(--stage);
    font-family: "Open Sans", sans-serif;
    position: relative;
  }
  .card {
    position: absolute;
    top: 200px;
    width: 540px;
    height: 310px;
    background: var(--card);
    border-radius: 22px;
    overflow: hidden;
    border-bottom: 4px solid var(--blue);
  }
  .card--back { left: 40px; }
  .card--front { left: 620px; }

  /* Back side */
  .brand {
    position: absolute;
    left: 0; right: 0;
    top: 108px;
    display: flex;
    align-items: center;
    justify-content: center;
    gap: 14px;
  }
  .brand__dot {
    width: 34px; height: 34px;
    border-radius: 50%;
    background: var(--coral);
  }
  .brand__name {
    font-family: "Montserrat", sans-serif;
    font-weight: 800;
    font-size: 58px;
    color: var(--blue);
    letter-spacing: 1px;
  }
  .tagline {
    position: absolute;
    left: 0; right: 0;
    top: 190px;
    text-align: center;
    font-family: "Montserrat", sans-serif;
    font-weight: 500;
    font-size: 15px;
    color: var(--ink);
    letter-spacing: .5px;
  }

  /* Front side */
  .front__brand {
    position: absolute;
    left: 26px;
    top: 120px;
    font-family: "Montserrat", sans-serif;
    font-weight: 800;
    font-size: 44px;
    color: var(--blue);
  }
  .divider {
    position: absolute;
    left: 262px;
    top: 40px;
    width: 1.5px;
    height: 200px;
    background: var(--blue);
  }
  .contact {
    position: absolute;
    left: 284px;
    top: 40px;
    color: var(--ink);
  }
  .contact__name {
    font-size: 22px;
    font-weight: 700;
    color: var(--blue);
    line-height: 1.1;
  }
  .contact__name span { color: var(--coral); font-weight: 400; }
  .contact__role { font-size: 14px; font-weight: 600; margin-top: 2px; }
  .contact__address { font-size: 11.5px; margin-top: 12px; line-height: 1.45; }
  .contact__list { list-style: none; margin-top: 14px; font-size: 11.5px; }
  .contact__list li { display: flex; align-items: center; gap: 8px; line-height: 1.8; }
  .contact__list svg { width: 13px; height: 13px; flex: none; }

  .band {
    position: absolute;
    bottom: 18px;
    height: 18px;
  }
  .band--blue { left: 0; width: 270px; background: var(--blue); }
  .band--coral { left: 270px; right: 0; background: var(--coral); }
</style>
</head>
<body>

<section class="card card--back" aria-label="Card back">
  <div class="brand">
    <span class="brand__dot"></span>
    <span class="brand__name">Vexalund</span>
  </div>
  <p class="tagline">Remedies of Life.</p>
</section>

<section class="card card--front" aria-label="Card front">
  <div class="front__brand">Vexalund</div>
  <div class="divider"></div>
  <div class="contact">
    <p class="contact__name">Arjun <span>K. Solanki</span></p>
    <p class="contact__role">CEO</p>
    <p class="contact__address">14, Neelkamal Nagar,<br>Amravati, 444601, India</p>
    <ul class="contact__list">
      <li>
        <svg viewBox="0 0 14 14"><rect x="3" y="1" width="8" height="12" rx="1.5" fill="none" stroke="#f0634d" stroke-width="1.4"/></svg>
        +919 500123487
      </li>
      <li>
        <svg viewBox="0 0 14 14"><circle cx="7" cy="7" r="5.8" fill="none" stroke="#29a6e0" stroke-width="1.4"/><path d="M1.5 7h11M7 1.2c-2.4 3.4-2.4 8.2 0 11.6M7 1.2c2.4 3.4 2.4 8.2 0 11.6" fill="none" stroke="#29a6e0" stroke-width="1.1"/></svg>
        www.vexalund.com
      </li>
      <li>
        <svg viewBox="0 0 14 14"><rect x="1" y="3" width="12" height="8.5" rx="1" fill="none" stroke="#f0634d" stroke-width="1.4"/><path d="M1.5 3.5 7 8l5.5-4.5" fill="none" stroke="#f0634d" stroke-width="1.2"/></svg>
        aksolanki@vexalund.com
      </li>
    </ul>
  </div>
  <div class="band band--blue"></div>
  <div class="band band--coral"></div>
</section>

</body>
</html>
```